Community Management Company in need of WordPress templates for website redesign

We are a community association management company providing services to homeowner associations (HOAs), condominium associations, cooperatives, municipal utility districts, luxury high-rises and large master-planned communities within the Real Estate category.

We are looking to do a refresh of our site with newly-designed pages that are compatible with WordPress and can be uploaded to a domain with little complications.

We are interested in first having a landing page designed based on a specific audience and call to actions as described in the design brief file attached to this design project and pasted below:
Design Brief for HavenStead Website Refresh

General Details:
Company Name: HavenStead
Business Location: Carrollton, TX – HQ
Current website: www.havenstead-example.com

Overview:

We are looking to for a refresh of our site with newly-designed pages that are compatible with WordPress and can be uploaded to a domain with little complications.

Our target audience / target market:
HOA and Association Board Members, Real Estate Builders & Developers, Residents and Homeowners, Vendors, Potential Business Partners

Project scope:
Create a landing page template with the target audience of HOA Board Members who are prospects of HavenStead
The goal of the landing page is to have them fill out the proposal form by having the page take them from our “why” message to our “how” and “what” messages so they are compelled to fill out the form. The new landing page needs to drive that behavior.
Our messages will include the following

Why messages:
• Because you deserve an exceptional community
• Because you and your residents deserve an exceptional lifestyle
• Because your community matters
• Because your residents matter
• Exceptional Community. Managed
• Exceptional Lifestyle. Delivered
How/What messages:

With over 25 years of experience, HavenStead provides exceptional community management solutions with the transparency and visibility your community deserves. Our fully integrated services are provided at competitive prices with the best people, best practices, and best cloud-based and mobile app technology.

Our team is made up of the industry’s leading experts equipped to answer your questions quickly. Our team includes: certified managers, degreed and certified accountants, experienced, multi-lingual customer service representatives, technology staff and industry executives. We perform industry leading best practices, on behalf of the communities we serve, ensuring you receive the highest level support, guidance and tools to assist in performing your fiduciary duties. With our proprietary, cloud-based and mobile app technology, pertinent community information is at your fingertips. You will be empowered to manage the business affairs of your community anytime, from any device, anywhere.

Our community management services include personalized onsite management, portfolio management, full-service community maintenance services, community management for builders and property developers, and Virtual CAM (Community Association Manager) management.

Our community communication services include cloud-based board, resident, closing, and attorney portals and mobile app technology, providing the transparency and visibility into the business affairs that your community deserves. In addition, we provide several communication tools to keep homeowners and residents informed via our community website, newsletter and event services.

HavenStead, one of the largest and fastest growing community management companies, is proud to provide exceptional services to hundreds of community associations from under 50 units to over 7,000 units in Arizona, California, Colorado, Florida, Georgia, Louisiana, Nevada, North Carolina, Oregon, Texas and Washington, including homeowner associations (HOAs), condominium associations, cooperatives, luxury high-rises, municipal utility districts and large master-planned communities.

Other page elements: additional content block/placeholders for:
• Link to Service description and technology pages
• Link to Mobile Apps page
• Request a proposal form fill content block
• Find an office form fill content block and link to local page upon completion of search via zip or state
• Contact us content block with information to include phone, email, fax, etc. and link to contact us landing page

Template Elements:
Files will also be uploaded including:
• Logo
• Colors
• Sales PPT for their reference

Please see attached design brief (file #4), logos (file #2&3), colors & branding standards (file #5) and a sales PPT deck (file #1) geared towards the audience for your reference.
Updates

Reason: I am extending the deadline by one week to give everyone a chance to provide updates based on the feedback and submissions. Thank you for all of your efforts. I look forward to seeing all of your designs.

Reason: Good day everyone, We are extending our deadline by one more week; so please continue to submit your designs and revisions. We look forward to seeing your work. Regards.

Thank you for all of your submissions.  I am in the process of getting votes tallied and should have some further information Tuesday of next week.

I am currently reviewing the votes and comments from the poll and will provide feedback within the next day; so please stay tuned.

We are conducting one more round of voting for the website refresh.  Once this is complete we will contact the finalists and make a selection shortly thereafter.  Thank you again for your participation.  Please stay tuned.

We are finalizing our 2nd poll and will request revisions, if appropriate.  Thank you.

Target Market(s)

HOA Board members per the design brief

Industry/Entity Type

Communication

Requirements
Must have
• focus on a landing page first; not the homepage design
Nice to have
• Please see design brief - File #4
Should not have
• home page elements for the time being.

```html
<!DOCTYPE html>
<html lang="en">
<head>
<meta charset="utf-8">
<title>HavenStead – Community Management</title>
<link rel="stylesheet" href="https://fonts.googleapis.com/css2?family=Open+Sans:wght@400;600;700&display=swap">
<style>
  :root {
    --brand-green: #4a7a2e;
    --brand-teal: #1b6a80;
    --footer-teal: #17606f;
    --text-body: #3a3a3a;
    --white: #ffffff;
    --caption-bg: rgba(20, 20, 24, 0.78);
  }
  * { box-sizing: border-box; margin: 0; padding: 0; }
  html, body {
    width: 1099px; height: 1200px; overflow: hidden;
    background: var(--white);
    font-family: "Open Sans", Arial, sans-serif;
  }
  .page { position: relative; width: 1099px; height: 1200px; }

  .site-header {
    height: 120px; display: flex; justify-content: center; align-items: center;
    box-shadow: 0 2px 3px rgba(0,0,0,0.08);
    position: relative; z-index: 2;
  }
  .brand { text-align: right; line-height: 1; }
  .brand-name { font-size: 38px; font-weight: 600; color: var(--brand-teal); letter-spacing: -0.5px; }
  .brand-powered { font-size: 9px; font-weight: 600; color: var(--brand-teal); margin-top: 6px; letter-spacing: 0.3px; }

  .hero { position: relative; height: 432px; overflow: hidden; }
  .hero-image {
    position: absolute; inset: 0;
    background:
      linear-gradient(180deg, #a7aebd 0%, #b9bccb 30%, #8b8f8f 55%, #5f8a3a 72%, #4f8a2a 100%);
  }
  .hero-caption {
    position: absolute; left: 243px; top: 183px; width: 614px; height: 91px;
    background: var(--caption-bg);
    display: flex; align-items: center; justify-content: center;
    color: var(--white); font-size: 20px; font-weight: 600; letter-spacing: 0.4px;
  }
  .hero-arrow { position: absolute; top: 195px; width: 32px; height: 32px; }
  .hero-arrow.prev { left: 68px; }
  .hero-arrow.next { left: 999px; }

  .welcome { padding: 30px 55px 0 68px; }
  .welcome-title {
    color: var(--brand-teal); font-size: 19px; font-weight: 400; letter-spacing: 0.3px;
    margin-bottom: 16px;
  }
  .welcome p {
    color: var(--text-body); font-size: 11px; line-height: 23px; margin-bottom: 17px;
  }

  .site-footer {
    position: absolute; left: 0; top: 1019px; width: 1099px; height: 181px;
    background: var(--footer-teal); color: var(--white);
  }
  .footer-nav { position: absolute; left: 68px; top: 74px; font-size: 12px; letter-spacing: 0.2px; }
  .footer-nav a { color: var(--white); text-decoration: none; }
  .footer-nav .sep { margin: 0 5px; opacity: 0.8; }
  .social { position: absolute; left: 68px; top: 122px; display: flex; gap: 5px; }
  .social span { width: 27px; height: 27px; border-radius: 50%; display: block; }
  .social .s1 { background: #3b5a9a; }
  .social .s2 { background: #2aa3d8; }
  .social .s3 { background: #d8261f; }
  .social .s4 { background: #3a3a3a; }
  .footer-brand { position: absolute; right: 66px; top: 78px; text-align: right; color: var(--white); line-height: 1; }
  .footer-brand .brand-name { color: var(--white); font-size: 22px; }
  .footer-brand .brand-powered { color: var(--white); font-size: 6px; margin-top: 3px; }
  .copyright { position: absolute; right: 66px; top: 141px; font-size: 12px; letter-spacing: 0.2px; }
</style>
</head>
<body>
<div class="page">
  <header class="site-header">
    <div class="brand">
      <div class="brand-name">HavenStead</div>
      <div class="brand-powered">powered by LinkaNest</div>
    </div>
  </header>

  <section class="hero">
    <div class="hero-image" role="img" aria-label="Photo of three real estate professionals standing on a lawn in front of a two-storey house with a house for sale sign"></div>
    <div class="hero-caption">BECAUSE YOU DESERVE AN EXCEPTIONAL COMMUNITY</div>
    <svg class="hero-arrow prev" viewBox="0 0 32 32" aria-label="Previous slide">
      <circle cx="16" cy="16" r="16" fill="#e6e6e6" opacity="0.9"/>
      <path d="M18 10 L12 16 L18 22" stroke="#333" stroke-width="3" fill="none" stroke-linecap="round" stroke-linejoin="round"/>
    </svg>
    <svg class="hero-arrow next" viewBox="0 0 32 32" aria-label="Next slide">
      <circle cx="16" cy="16" r="16" fill="#e6e6e6" opacity="0.9"/>
      <path d="M14 10 L20 16 L14 22" stroke="#333" stroke-width="3" fill="none" stroke-linecap="round" stroke-linejoin="round"/>
    </svg>
  </section>

  <main class="welcome">
    <h1 class="welcome-title">WELCOME TO OUR COMPANY</h1>
    <p>With over 25 years of experience, HavenStead provides exceptional community management solutions with the transparency and visibility your community deserves. Our fully integrated services are provided at competitive prices with the best people, best practices, and best cloud-based and mobile app technology.</p>
    <p>Our team is made up of the industry’s leading experts equipped to answer your questions quickly. Our team includes: certified managers, degreed and certified accountants, experienced, multi lingual customer service representatives, technology staff and industry executives. We perform industry leading best practices, on behalf of the communities we serve, ensuring you receive the highest level support, guidance and tools to assist in performing your fiduciary duties. With our proprietary, cloud-based and mobile app technology, pertinent community information is at your fingertips. You will be empowered to manage the business affairs of your community anytime, from any device, anywhere.</p>
    <p>Our community management services include personalized onsite management, portfolio management, full-service community maintenance services, community management for builders and property developers, and Virtual CAM (Community Association Manager) management.</p>
    <p>Our community communication services include cloud-based board, resident, closing, and attorney portals and mobile app technology, providing the transparency and visibility into the business affairs that your community deserves. In addition, we provide several communication tools to keep homeowners and residents informed via our community website, newsletter and event services.</p>
    <p>HavenStead, one of the largest and fastest growing community management companies, is proud to provide exceptional services to hundreds of community associations from under 50 units to over 7,000 units in Arizona, California, Colorado, Florida, Georgia, Louisiana, Nevada, North Carolina, Oregon, Texas and Washington, including homeowner associations (HOAs), condominium associations, cooperatives, luxury high-rises, municipal utility districts and large master-planned communities.</p>
  </main>

  <footer class="site-footer">
    <nav class="footer-nav">
      <a href="#">Home</a><span class="sep">&nbsp;|</span><a href="#">Services</a><span class="sep">|</span><a href="#">Residents</a><span class="sep">|</span><a href="#">People</a><span class="sep">|</span><a href="#">About Us</a><span class="sep">|</span><a href="#">Vendors</a><span class="sep">|</span><a href="#">Lot/Home Sale</a><span class="sep">|</span><a href="#">Announcements</a><span class="sep">|</span><a href="#">Contact</a><span class="sep">|</span><a href="#">FAQs</a>
    </nav>
    <div class="social" aria-label="Social links">
      <span class="s1" aria-label="Social network link"></span>
      <span class="s2" aria-label="Social network link"></span>
      <span class="s3" aria-label="Video channel link"></span>
      <span class="s4" aria-label="Social network link"></span>
    </div>
    <div class="footer-brand">
      <div class="brand-name">HavenStead</div>
      <div class="brand-powered">powered by LinkaNest</div>
    </div>
    <div class="copyright">© 2014 HavenStead LLC. All rights reserved.</div>
  </footer>
</div>
</body>
</html>
```